Annual Report Velomar 2025

Take a PowerPoint presentation and turn it into a info graphic type annual report, posters and flyers.

Annual report ideally no more than 8 pages.

Please use the colours and fonts in the attached brand guidelines.

We are looking for an infographic visually appealing piece.

```html
<!DOCTYPE html>
<html lang="en">
<head>
<meta charset="utf-8">
<title>Velomar Annual Report 2025 – Revenue Development</title>
<link href="https://fonts.googleapis.com/css2?family=Playfair+Display:wght@400;700&family=Poppins:wght@400;600&display=swap" rel="stylesheet">
<style>
  :root {
    --navy: #0e2f58;
    --green: #7a9e2b;
    --green-light: #dde7c9;
    --slate-light: #dde2e9;
    --ink: #1d1d1d;
    --white: #ffffff;
  }
  * { margin: 0; padding: 0; box-sizing: border-box; }
  html, body { width: 927px; height: 1200px; overflow: hidden; background: var(--white); }
  .page { position: relative; width: 927px; height: 1200px; font-family: "Poppins", sans-serif; color: var(--ink); }

  .running-head { position: absolute; top: 52px; left: 57px; width: 812px; display: flex; align-items: center; gap: 8px; }
  .running-head .rule { flex: 1; height: 1px; background: var(--green); }
  .running-head .tagline { font-family: "Playfair Display", serif; color: var(--green); font-size: 19px; letter-spacing: 0.4px; }

  .section-title { font-family: "Playfair Display", serif; font-weight: 700; color: var(--navy); font-size: 39px; line-height: 1.15; letter-spacing: -0.3px; }
  .revenue-title { position: absolute; top: 128px; left: 56px; }

  .body-copy { font-size: 18px; line-height: 27.3px; text-align: justify; }
  .revenue-copy { position: absolute; top: 193px; left: 57px; width: 812px; }
  .revenue-copy p + p { margin-top: 8px; }

  .alt-band { position: absolute; top: 463px; left: 0; width: 927px; height: 387px; background: var(--green); overflow: hidden; }
  .alt-title { position: absolute; top: 17px; left: 55px; color: var(--white); font-size: 39px; line-height: 45px; }
  .alt-copy { position: absolute; top: 118px; left: 57px; width: 440px; color: var(--white); }
  .bond-photo { position: absolute; top: 34px; left: 534px; width: 335px; height: 320px; border-radius: 11px;
    background: radial-gradient(circle at 45% 50%, #d9d9d9 0%, #9a9a9a 45%, #4a4a4a 100%); }

  .highlights-title { position: absolute; top: 872px; left: 56px; }
  .highlights { position: absolute; top: 953px; left: 0; width: 927px; }
  .highlight { position: absolute; width: 180px; margin-left: -90px; text-align: center; }
  .highlight svg { display: block; margin: 0 auto 12px; }
  .highlight p { font-size: 18px; line-height: 27.3px; color: var(--ink); }
  .highlight strong { font-weight: 600; }

  .page-foot { position: absolute; top: 1118px; left: 57px; width: 812px; display: flex; align-items: center; }
  .page-foot .rule { flex: 1; height: 1px; background: var(--green); }
  .page-number { width: 36px; height: 28px; background: var(--green); color: var(--white); font-family: "Playfair Display", serif; font-size: 19px; line-height: 28px; text-align: center; }
</style>
</head>
<body>
<div class="page">
  <header class="running-head">
    <span class="rule"></span>
    <span class="tagline">Values Driving Value</span>
  </header>

  <h1 class="section-title revenue-title">Revenue Development</h1>
  <div class="body-copy revenue-copy">
    <p>Velomar is proud to offer a number of resources to support and encourage philanthropy. Velomar’ experts offer strategic planning and tactical planning for annual and capital fundraising donor and stakeholder engagement efforts and have increasingly been called up to resource fundraising efforts through a cost-recovery arrangement.</p>
    <p>Historically, Velomar has offered counsel and support for those looking to consider charitable giving as part of their estate planning. Be it bequests, gifts of securities, gifts or insurance or other estate or planning giving vehicles Velomar has the professional expertise to assist. These services delivered through our Velomar (LPG) effort are offered free-of-charge.</p>
  </div>

  <section class="alt-band">
    <h2 class="section-title alt-title">Alternative Revenue<br>Opportunities</h2>
    <p class="body-copy alt-copy">Alternative revenue strategies take many forms, one that is growing in popularity are “community bonds”. Available to NGOs, community bonds are interest bearing bonds typically intended for small-scale, e.g., &lt;$100MM, social investment projects, non-accredited investors. Similar in many ways to a traditional bond, they are an interest-bearing loan from an investor, which has a set rate of return and a fixed term.</p>
    <div class="bond-photo" role="img" aria-label="Close-up black and white photo of an engraved bond certificate with the word BOND"></div>
  </section>

  <h2 class="section-title highlights-title">Velomar 2025 Highlights</h2>
  <div class="highlights">
    <div class="highlight" style="left:121px">
      <svg width="64" height="64" viewBox="0 0 64 64"><circle cx="32" cy="32" r="30" fill="var(--slate-light)"/><rect x="21" y="21" width="22" height="22" rx="2" fill="var(--navy)"/><polyline points="23,37 29,31 33,35 41,26" fill="none" stroke="var(--white)" stroke-width="2"/></svg>
      <p>New Money<br><strong>Market<br>Portfolio</strong></p>
    </div>
    <div class="highlight" style="left:298px">
      <svg width="64" height="64" viewBox="0 0 64 64"><circle cx="32" cy="32" r="30" fill="var(--green-light)"/><circle cx="32" cy="32" r="16" fill="var(--white)" stroke="var(--green)" stroke-width="3.5"/><text x="32" y="40" text-anchor="middle" font-family="Poppins, sans-serif" font-weight="600" font-size="21" fill="var(--green)">$</text></svg>
      <p>Reached<br><strong>$100 million</strong> in<br>assets</p>
    </div>
    <div class="highlight" style="left:468px">
      <svg width="64" height="64" viewBox="0 0 64 64"><circle cx="32" cy="32" r="30" fill="var(--slate-light)"/><circle cx="32" cy="32" r="15" fill="var(--navy)"/><text x="32" y="37" text-anchor="middle" font-family="Poppins, sans-serif" font-weight="600" font-size="14" fill="var(--white)">$</text></svg>
      <p>Granted <strong>$6<br>million</strong> to<br>partners</p>
    </div>
    <div class="highlight" style="left:636px">
      <svg width="64" height="64" viewBox="0 0 64 64"><circle cx="32" cy="32" r="30" fill="var(--green-light)"/><rect x="21" y="18" width="18" height="24" fill="var(--green)"/><circle cx="40" cy="38" r="5" fill="none" stroke="var(--navy)" stroke-width="2.5"/><line x1="44" y1="42" x2="48" y2="46" stroke="var(--navy)" stroke-width="3"/></svg>
      <p>New <strong>Case<br>Studies</strong><br>Series</p>
    </div>
    <div class="highlight" style="left:794px">
      <svg width="64" height="64" viewBox="0 0 64 64"><circle cx="32" cy="32" r="30" fill="var(--slate-light)"/><rect x="19" y="20" width="26" height="18" fill="none" stroke="var(--navy)" stroke-width="3"/><path d="M32 22 l4 8 h-8 z" fill="var(--navy)"/><rect x="30" y="38" width="4" height="5" fill="var(--navy)"/><rect x="25" y="43" width="14" height="2.5" fill="var(--navy)"/></svg>
      <p><strong>Launch<br>Bookkeeping</strong><br>Services</p>
    </div>
  </div>

  <footer class="page-foot">
    <span class="rule"></span>
    <span class="page-number">05</span>
  </footer>
</div>
</body>
</html>
```